LEARN Business Skills so you can Earn a good living

size of the poster is 8”x 10.75" plus 0.25" bleed.
Please leave 1 inch on the bottoum for footer
I want a design a poster that will attract people's attention.
I appreciate a creative ad however the ad should not take away from being able to clearly read the text.
-I also appreciate a simple creative ad that is not too busy.
-you can use graphics, vectors, or pictures of real people.
-however, if you use real people it should be a white male that is wearing a white shirt and look like a professional person.

Target Market(s)

Potential young business people

Industry/Entity Type

education

Requirements
Must have
• easy to read the text
Nice to have
• I would like a "creative" simple ad that is easy to be read
Should not have
• pictures of women

```html
<!DOCTYPE html>
<html lang="en">
<head>
<meta charset="UTF-8">
<title>Learn It to Earn It – Business Enrichment Course</title>
<link href="https://fonts.googleapis.com/css2?family=Montserrat:wght@400;500;700;800;900&family=Dancing+Script:wght@700&display=swap" rel="stylesheet">
<style>
  :root {
    --stage: #f2f2f2;
    --paper: #fbfaf8;
    --navy: #2e3247;
    --orange-line: #f0aa5e;
    --band-strong: #f5c890;
    --band-soft: rgba(247, 214, 170, 0);
    --footer-tint: #fdf0e6;
    --photo-light: #f3efea;
    --photo-mid: #e7dccd;
    --photo-warm: #c9ad8c;
  }
  * { margin: 0; padding: 0; box-sizing: border-box; }
  html, body {
    width: 1200px; height: 1200px; overflow: hidden;
    background: var(--stage);
  }
  .poster {
    position: absolute; left: 177px; top: 40px;
    width: 846px; height: 1120px;
    background: linear-gradient(180deg, #fdfdfc 0%, var(--paper) 60%, #f7f5f2 100%);
    overflow: hidden;
    color: var(--navy);
  }
  .headline {
    position: absolute; right: 54px;
    font-family: "Montserrat", sans-serif; font-weight: 900;
    font-size: 152px; line-height: 1; letter-spacing: -1px;
    white-space: nowrap;
  }
  .headline--learn { top: 46px; }
  .headline--earn { top: 160px; }
  .headline__connector {
    position: absolute; left: 50px; top: 168px;
    font-family: "Dancing Script", cursive; font-weight: 700;
    font-size: 138px; line-height: 1; letter-spacing: -4px;
  }
  .course-title {
    position: absolute; left: 54px; top: 376px;
    font-family: "Montserrat", sans-serif; font-weight: 700;
    font-size: 64px; line-height: 65px; letter-spacing: -0.5px;
  }
  .tagline {
    position: absolute; left: 56px; top: 598px;
    font-family: "Montserrat", sans-serif; font-weight: 700;
    font-size: 19px; line-height: 30px;
  }
  .benefits {
    position: absolute; left: 56px; top: 674px;
    font-family: "Montserrat", sans-serif;
    font-size: 19.5px; line-height: 30px;
  }
  .benefits__lead { font-weight: 700; }
  .benefits__list { font-weight: 400; }
  .topic-band {
    position: absolute; left: 0; top: 837px;
    width: 846px; height: 179px;
    background: linear-gradient(90deg, var(--band-strong) 0%, #f6d4a8 45%, var(--band-soft) 80%);
    border-top: 3px solid var(--orange-line);
    border-bottom: 4px solid var(--orange-line);
  }
  .topic-band__list {
    position: absolute; left: 56px; top: 34px; width: 460px;
    font-family: "Montserrat", sans-serif; font-weight: 500;
    font-size: 11.6px; line-height: 20.2px; text-transform: uppercase;
    white-space: pre-line;
  }
  .footer-zone {
    position: absolute; left: 0; top: 1016px;
    width: 846px; height: 104px;
    background: linear-gradient(90deg, var(--footer-tint) 0%, #fdf8f4 50%, #ffffff 100%);
  }
  .hero-photo {
    position: absolute; left: 520px; top: 316px;
    width: 326px; height: 700px;
  }
</style>
</head>
<body>
  <div class="poster">
    <div class="headline headline--learn">LEARN IT</div>
    <div class="headline__connector">to</div>
    <div class="headline headline--earn">EARN IT</div>

    <h1 class="course-title">Business<br>Enrichment<br>Course</h1>

    <p class="tagline">A proven success of helping people<br>in their livelihoods</p>

    <div class="benefits">
      <p class="benefits__lead">Business skills that will help you:</p>
      <p class="benefits__list">Get a quality job - start / grow your<br>business-Increase your salary</p>
    </div>

    <div class="topic-band">
      <p class="topic-band__list">Business admiistration – small business management -
Finance - investments - computers- accounting - sales
Marketing - project management interviewing skills - business
law -negotiation – public speaking - import/export - information
technoloy -distribution - marketing -   ledgerwise - real
estate - health care-management - shopvale</p>
    </div>

    <svg class="hero-photo" viewBox="0 0 326 700" role="img" aria-label="Photo of a smiling professional man in glasses, white shirt and khaki trousers giving a thumbs up">
      <defs>
        <linearGradient id="photoTone" x1="0" y1="0" x2="0" y2="1">
          <stop offset="0" stop-color="var(--photo-light)" stop-opacity="0"/>
          <stop offset="0.15" stop-color="var(--photo-mid)" stop-opacity="0.9"/>
          <stop offset="0.8" stop-color="var(--photo-mid)"/>
          <stop offset="1" stop-color="var(--photo-warm)"/>
        </linearGradient>
      </defs>
      <rect x="0" y="0" width="326" height="700" fill="url(#photoTone)"/>
    </svg>

    <div class="footer-zone"></div>
  </div>
</body>
</html>
```